Need a Wordpress website for my HVAC company

I need a Wordpress website created for an HVAC company in a competitive market.
Following are some websites I like:
My current website is www.borvicoheating.com - we also have a facebook page with some pictures

We are an airconditioning and heating company that does both residential and commmercial work.
We need the following info on our website:
-mobile friendly
-Schedule an appt -repair/maintnenace/installation (i would like this option to always be on the page even if they scroll down.)
-24 hour service
-coupons /promotions
-financing
-reviews/testimonials
-about
-blog
-Our service area
The following are services we provide:
-Air conditioning - Installation/Service/Maintenance/new construction
-Heating - Installation/Service/Maintenance/new construction ( gas furnace, 2 stage furnace, electric heat)
-Duct - Repair/Replacement/Istallation - (zone systems)
-thermostats (wifi)
-Heat pump
-Air handler
-self communicating systems
-carbon monoxide testing
-hail damage
-duct sealing
-insulation
-Air cleaners - UV Air purifiers
-humidifiers

I would also like Quilbo SEO add on

Target Market(s)

Anyone who needs our services HVAC contractor

Industry/Entity Type

Hvac

Contact Information for Business Card

Phone:480-555-2046
website:www.borvicoheating.com
email pmarsh@borvicoheating.com

Coding

Coded - Design and coding required

Number of Pages Required

5+ page

Font styles to use
Serif
Sans Serif

Requirements
Must have
• I wrote in brief. I already have Webly Nest. Long story I paid for 3 years already. I need someone to put website there. Ive never used Wordpress but would like a template page so I can easily add services.
Nice to have
• Clean, bright, original

```html
<!DOCTYPE html>
<html lang="en">
<head>
<meta charset="utf-8">
<title>Borvico Heating – Air Conditioning &amp; Heating</title>
<link href="https://fonts.googleapis.com/css2?family=Open+Sans:wght@400;600;700&family=Roboto:wght@400;500;700&display=swap" rel="stylesheet">
<style>
:root{
  --blue:#1a73c9;
  --blue-deep:#0f4f95;
  --blue-light:#3d9be9;
  --red:#e0262b;
  --green:#2aa84a;
  --ink:#333a44;
  --muted:#7b8490;
  --dark:#3a4048;
  --line:#e2e6ea;
  --white:#fff;
}
*{box-sizing:border-box;margin:0;padding:0}
html,body{width:1200px;height:2180px;overflow:hidden}
body{font-family:"Open Sans",Arial,sans-serif;color:var(--ink);background:#fff;position:relative}
h1,h2,h3,.nav,.label{font-family:"Roboto",Arial,sans-serif}

/* header / hero */
.hero{position:absolute;left:0;top:0;width:1200px;height:560px}
.hero-photo{position:absolute;inset:0;background:linear-gradient(180deg,#4f8fc4 0%,#8fb7d3 35%,#b7a58e 62%,#7a756e 82%,#4a5660 100%)}
.hero-shade{position:absolute;inset:0;background:linear-gradient(180deg,rgba(10,40,80,.35),rgba(10,40,80,0) 30%,rgba(20,60,110,.25) 100%)}
.topbar{position:absolute;left:0;top:0;width:100%;height:62px;display:flex;align-items:center;padding:0 40px}
.brand{display:flex;align-items:center;gap:10px;font-family:"Roboto",sans-serif;font-weight:700;font-size:22px;color:var(--white)}
.brand-dot{width:34px;height:34px;border-radius:50%;background:var(--red)}
.nav{margin-left:auto;display:flex;align-items:center;gap:30px;font-size:12px;font-weight:500;color:var(--white);letter-spacing:.5px}
.nav .btn{padding:7px 12px;border-radius:3px;font-size:11px}
.btn-call{background:var(--red);margin-left:-6px}
.btn-quote{background:var(--white);color:var(--ink)}

.cards{position:absolute;top:420px;left:175px;display:flex;gap:20px}
.card{width:270px;height:185px;position:relative;background:rgba(30,50,75,.72);padding-top:50px;text-align:center;color:#e8eef5;font-size:11px;line-height:1.5}
.card p{padding:0 22px}
.card .icon{position:absolute;top:-36px;left:50%;margin-left:-36px;width:72px;height:72px;border-radius:50%;display:flex;align-items:center;justify-content:center;border:4px solid rgba(255,255,255,.85)}
.card .bar{position:absolute;bottom:0;left:0;right:0;height:44px;display:flex;align-items:center;justify-content:center;color:var(--white);font-weight:700;font-size:13px;letter-spacing:1px;font-family:"Roboto",sans-serif}
.repair .icon,.repair .bar{background:var(--red)}
.maint .icon,.maint .bar{background:var(--green)}
.install .icon,.install .bar{background:var(--blue)}

/* services strip */
.services{position:absolute;top:620px;left:0;width:1200px;height:180px;background:linear-gradient(90deg,var(--blue-deep),var(--blue) 50%,var(--blue-light));display:flex;justify-content:center;padding-top:55px}
.service{width:150px;text-align:center;color:var(--white);font-family:"Roboto",sans-serif;font-size:15px;font-weight:500}
.service svg{display:block;margin:0 auto 14px}

/* service area */
.area{position:absolute;top:820px;left:0;width:1200px;text-align:center}
.section-title{font-size:24px;font-weight:500;color:var(--ink);line-height:30px}
.section-title span{color:var(--blue)}
.title-rule{width:60px;height:2px;background:var(--blue);margin:10px auto 0}
.tiles{display:flex;justify-content:center;gap:20px;margin-top:32px}
.tile{width:240px}
.tile .img{height:150px}
.tile .label{background:var(--blue);color:var(--white);font-weight:700;font-size:13px;letter-spacing:1px;height:38px;line-height:38px}
.img-res{background:linear-gradient(180deg,#8cb8da,#c9c0a6 60%,#6e7e5a)}
.img-com{background:linear-gradient(180deg,#a9c9e4,#d8d2c4 55%,#8a8a80)}
.img-energy{background:linear-gradient(180deg,#5f8fc2,#3b5f8a 55%,#2d3b4d)}
.img-sched{background:linear-gradient(180deg,#dfe7ee,#f0f3f6 50%,#c7ccd2)}

/* about + mail */
.split{position:absolute;top:1100px;left:0;width:1200px;height:330px;display:flex}
.about{width:600px;background:linear-gradient(135deg,var(--blue-deep),var(--blue));color:var(--white);padding:36px 90px 0 130px;text-align:center}
.about h2,.mail h2{font-size:24px;font-weight:500}
.about .title-rule,.mail .title-rule{background:var(--white)}
.about p{font-size:12.5px;line-height:1.75;margin-top:20px}
.btn-outline{display:inline-block;margin-top:20px;border:1px solid var(--white);padding:8px 16px;font-size:11px;font-weight:700;letter-spacing:1px}
.mail{width:600px;background:var(--dark);color:var(--white);padding:36px 110px 0 60px;text-align:center}
.form{margin-top:28px;display:grid;grid-template-columns:1fr 1fr 1fr;gap:10px;text-align:left}
.field{background:var(--white);height:30px;font-size:11px;color:#9aa1aa;padding:8px 10px}
.field.msg{grid-column:1/4;height:100px}
.send{grid-column:3;justify-self:end;background:var(--blue);color:var(--white);font-size:10px;font-weight:700;padding:8px 14px;letter-spacing:.5px}

/* testimonials */
.reviews{position:absolute;top:1460px;left:0;width:1200px;text-align:center}
.review-grid{width:1000px;margin:30px auto 0;display:grid;grid-template-columns:1fr 1fr;text-align:left}
.review{display:flex;align-items:center;gap:24px;padding:16px 30px;height:112px}
.review:nth-child(odd){border-right:1px solid var(--line);flex-direction:row-reverse;text-align:right}
.review:nth-child(-n+2){border-bottom:1px solid var(--line)}
.avatar{flex:0 0 70px;height:70px;border-radius:50%;background:linear-gradient(135deg,#c9b8a6,#8a7a6e)}
.review p{font-size:11.5px;line-height:1.6;color:var(--muted)}
.review .who{display:block;margin-top:6px;color:var(--ink);font-size:11px}

/* footer */
.footer{position:absolute;top:1810px;left:0;width:1200px;height:370px;background:linear-gradient(180deg,var(--blue-light),var(--blue) 40%,var(--blue-deep));color:var(--white);text-align:center}
.skyline{position:absolute;top:-34px;left:0;width:1200px;height:34px;background:linear-gradient(180deg,rgba(61,155,233,0),var(--blue-light))}
.social{display:flex;justify-content:center;gap:34px;padding-top:60px}
.social span{width:22px;height:22px;border-radius:50%;background:var(--white)}
.footer .brand{justify-content:center;margin-top:42px;font-size:26px}
.contact{margin-top:46px;font-size:11px}
.contact b{font-weight:700;margin-right:4px}
.contact span{margin:0 8px}
.copy{margin-top:10px;font-size:10px;opacity:.8}
</style>
</head>
<body>

<header class="hero">
  <div class="hero-photo" role="img" aria-label="Photo of a suburban house with company service vans parked in the driveway and a technician waving"></div>
  <div class="hero-shade"></div>
  <div class="topbar">
    <div class="brand"><span class="brand-dot"></span>Borvico Heating</div>
    <nav class="nav">
      <span>ABOUT US</span><span>SERVICES</span><span>FINANCING</span><span>PROMOTIONS</span><span>BLOG</span><span>CONTACT</span>
      <span class="btn btn-call">CALL US</span>
      <span class="btn btn-quote">Request a Quote</span>
    </nav>
  </div>
  <div class="cards">
    <div class="card repair">
      <div class="icon"><svg width="32" height="32" viewBox="0 0 24 24" fill="none" stroke="#fff" stroke-width="2" stroke-linecap="round"><path d="M14.5 5.5a4 4 0 0 0 5 5L12 18l-3 3-3-3 3-3 7.5-7.5"/><path d="M4 4l6 6"/></svg></div>
      <p>Fast same-day repairs for any cooling or heating system, done right the first time by our team.</p>
      <div class="bar">REPAIR</div>
    </div>
    <div class="card maint">
      <div class="icon"><svg width="30" height="30" viewBox="0 0 24 24" fill="none" stroke="#fff" stroke-width="2" stroke-linecap="round"><rect x="5" y="4" width="14" height="17" rx="1"/><path d="M9 4V2h6v2M9 12l2 2 4-4"/></svg></div>
      <p>Regular tune-ups keep your unit efficient, lower your bills and extend its working life.</p>
      <div class="bar">MAINTENANCE</div>
    </div>
    <div class="card install">
      <div class="icon"><svg width="30" height="30" viewBox="0 0 24 24" fill="none" stroke="#fff" stroke-width="2" stroke-linecap="round"><path d="M20 12a8 8 0 0 1-14 5M4 12a8 8 0 0 1 14-5"/><path d="M18 3v4h-4M6 21v-4h4"/></svg></div>
      <p>New system installs sized for your home or business, with clean work and fair pricing.</p>
      <div class="bar">INSTALLATION</div>
    </div>
  </div>
</header>

<section class="services">
  <div class="service"><svg width="44" height="44" viewBox="0 0 24 24" fill="none" stroke="#fff" stroke-width="1.6" stroke-linecap="round"><path d="M12 2v20M3 7l18 10M21 7L3 17M9 3l3 2 3-2M9 21l3-2 3 2"/></svg>Air Conditioning</div>
  <div class="service"><svg width="44" height="44" viewBox="0 0 24 24" fill="none" stroke="#fff" stroke-width="1.6"><rect x="3" y="5" width="18" height="14" rx="1"/><circle cx="10" cy="12" r="4"/><path d="M17 8v8"/></svg>Heat Pump</div>
  <div class="service"><svg width="44" height="44" viewBox="0 0 24 24" fill="none" stroke="#fff" stroke-width="1.6" stroke-linecap="round"><path d="M7 15a4 4 0 0 1 0-8 5 5 0 0 1 9.5 1.5A3.5 3.5 0 0 1 17 15z"/><circle cx="8" cy="19" r=".8"/><circle cx="12" cy="21" r=".8"/><circle cx="16" cy="19" r=".8"/></svg>Hail Damage</div>
  <div class="service"><svg width="44" height="44" viewBox="0 0 24 24" fill="none" stroke="#fff" stroke-width="1.6"><path d="M2 9h10v6H2zM12 7h4v10h-4zM16 9h6v6h-6z"/></svg>Duct sealing</div>
  <div class="service"><svg width="44" height="44" viewBox="0 0 24 24" fill="none" stroke="#fff" stroke-width="1.6"><circle cx="12" cy="12" r="9"/><circle cx="12" cy="12" r="1.5"/><path d="M12 10.5c0-3 1-5 3-5M13.5 12c3 0 5 1 5 3M12 13.5c0 3-1 5-3 5M10.5 12c-3 0-5-1-5-3"/></svg>Air Cleaners</div>
  <div class="service"><svg width="44" height="44" viewBox="0 0 24 24" fill="none" stroke="#fff" stroke-width="1.6"><path d="M12 3s6 7 6 11a6 6 0 0 1-12 0c0-4 6-11 6-11z"/></svg>Humidifiers</div>
</section>

<section class="area">
  <h2 class="section-title">Our <span>Service Area</span></h2>
  <div class="title-rule"></div>
  <div class="tiles">
    <div class="tile"><div class="img img-res" role="img" aria-label="Photo of a residential home"></div><div class="label">RESIDENTIAL</div></div>
    <div class="tile"><div class="img img-com" role="img" aria-label="Photo of a commercial building"></div><div class="label">COMMERCIAL</div></div>
    <div class="tile"><div class="img img-energy" role="img" aria-label="Photo of a house with solar panels"></div><div class="label">ENERGY</div></div>
    <div class="tile"><div class="img img-sched" role="img" aria-label="Photo of a company service van"></div><div class="label">SCHEDULE</div></div>
  </div>
</section>

<section class="split">
  <div class="about">
    <h2>About Us</h2>
    <div class="title-rule"></div>
    <p>Borvico Heating is a family run cooling and heating company based in Sorrel Flats. We handle repair, service, maintenance and new installs for homes and businesses alike. Our team covers Sorrel Flats, Dunmere, Halvet, Cressida Park, Oakhollow, Brennick, Marlow Ridge, Pellan and the wider Amberline Valley.</p>
    <span class="btn-outline">LEARN MORE</span>
  </div>
  <div class="mail">
    <h2>Feel Free to Mail</h2>
    <div class="title-rule"></div>
    <div class="form">
      <div class="field">Name *</div>
      <div class="field">Email *</div>
      <div class="field">Subject</div>
      <div class="field msg">Write Your Message Here</div>
      <div class="send">SEND MESSAGE</div>
    </div>
  </div>
</section>

<section class="reviews">
  <h2 class="section-title">What <span>People Say</span></h2>
  <div class="title-rule"></div>
  <div class="review-grid">
    <div class="review"><div class="avatar" role="img" aria-label="Customer portrait"></div><p>The crew arrived on time, found the fault quickly and had our cooling back on before dinner. Friendly, tidy and honest about the price.<span class="who">Owen Pratt , Developer</span></p></div>
    <div class="review"><div class="avatar" role="img" aria-label="Customer portrait"></div><p>Our new furnace was installed in one day. They explained every option and never pushed us toward the costly one.<span class="who">Nadia Voss , Designer</span></p></div>
    <div class="review"><div class="avatar" role="img" aria-label="Customer portrait"></div><p>We use their maintenance plan for the office. Bills dropped and we have not had a single breakdown all summer long.<span class="who">Clara Bennet , Creative Designer</span></p></div>
    <div class="review"><div class="avatar" role="img" aria-label="Customer portrait"></div><p>Called late on a Sunday and a technician came out within the hour. Great service from start to finish.<span class="who">Ravi Holm , Operations Manager</span></p></div>
  </div>
</section>

<footer class="footer">
  <div class="skyline" role="img" aria-label="City skyline silhouette"></div>
  <div class="social"><span></span><span></span><span></span><span></span></div>
  <div class="brand"><span class="brand-dot"></span>Borvico Heating</div>
  <div class="contact">
    <span><b>Phone:</b>604-555-0182</span>
    <span><b>Fax:</b>604-555-0197</span>
    <span><b>Address:</b>88 Larkfield Road, Sorrel Flats</span>
    <span><b>Email:</b>hello@borvicoheating.com</span>
  </div>
  <div class="copy">Copyright 2020. All Rights Reserved by Borvico Heating</div>
</footer>

</body>
</html>
```